Anzeigengestaltung für Verkauf & Installation von Alarmanlagen und Videoüberwachungssystemen
Zielgruppe
Verkauf und Installation von Alarmanlagen und Videoüberwachungssystemen.
Verkauf erfolgt über eigenen Onlineshop.
Installation der Anlagen im regionalen Umkreis, hauptsächlich Privatkunden.
Zielgruppe: Privatkunden, Familien, mit vorhandener Immobilie/Wohneigentum.
Aufgabenstellung
Zeitungsformat:
92 mm x 60 mm
s/w-4C
Text Entwurf als Orientierung befindet sich im Anhang, ebenso das Firmenlogo.
Bilder aus der Webseite sind ebenfalls beigefügt. Vielleicht lässt sich damit etwas anfangen, ich bin aber auch für Vorschläge aus geeigneten Stock-Bildern offen.

```html
<!DOCTYPE html>
<html lang="de">
<head>
<meta charset="utf-8">
<title>Wachturm Technik – Anzeige</title>
<link rel="stylesheet" href="https://fonts.googleapis.com/css2?family=Fira+Sans+Condensed:wght@500;600&family=Open+Sans:wght@400;600&display=swap">
<style>
  :root {
    --page: #f1f1f1;
    --panel-light: #f6f6f6;
    --panel-mid: #e6e6e6;
    --brand-red: #d8412f;
    --ink: #222222;
    --ink-soft: #555555;
    --white: #ffffff;
  }
  html, body {
    margin: 0;
    padding: 0;
    width: 1200px;
    height: 2400px;
    overflow: hidden;
    background: var(--page);
  }
  .ad {
    position: absolute;
    left: 50px;
    top: 841px;
    width: 1100px;
    height: 718px;
    overflow: hidden;
    background: linear-gradient(135deg, var(--panel-mid), var(--panel-light) 55%, var(--panel-mid));
    font-family: "Fira Sans Condensed", sans-serif;
    color: var(--ink);
  }
  .ad__shapes { position: absolute; inset: 0; }
  .brand {
    position: absolute;
    left: 594px;
    top: 72px;
    display: flex;
    align-items: center;
    gap: 18px;
  }
  .brand__dot {
    width: 80px; height: 80px;
    border-radius: 50%;
    background: var(--ink);
  }
  .brand__name {
    font-family: "Fira Sans Condensed", sans-serif;
    font-weight: 600;
    font-size: 44px;
    line-height: 1;
    color: var(--ink);
  }
  .brand__claim {
    font-family: "Open Sans", sans-serif;
    font-size: 13px;
    font-weight: 600;
    color: var(--ink-soft);
    margin-top: 6px;
  }
  .headline {
    position: absolute;
    left: 601px;
    top: 242px;
    margin: 0;
    font-weight: 600;
    font-size: 37px;
    letter-spacing: 0.2px;
    color: var(--ink);
  }
  .benefits {
    position: absolute;
    left: 600px;
    top: 298px;
    margin: 0;
    padding: 0;
    list-style: none;
  }
  .benefits li {
    display: flex;
    align-items: center;
    gap: 14px;
    height: 42px;
    font-weight: 500;
    font-size: 31px;
    color: var(--brand-red);
  }
  .benefits svg { width: 30px; height: 30px; }
  .funding {
    position: absolute;
    left: 583px;
    top: 460px;
    width: 517px;
    height: 66px;
    border-radius: 33px 0 0 33px;
    background: var(--brand-red);
    color: var(--white);
    font-weight: 500;
    font-size: 37px;
    line-height: 66px;
    padding-left: 52px;
    box-sizing: border-box;
  }
  .services {
    position: absolute;
    left: 596px;
    top: 556px;
    display: flex;
    gap: 26px;
    align-items: center;
  }
  .service {
    display: flex;
    align-items: center;
    gap: 8px;
    font-weight: 600;
    font-size: 24px;
  }
  .service svg { height: 38px; }
  .contact {
    position: absolute;
    right: 27px;
    top: 622px;
    text-align: right;
    font-family: "Open Sans", sans-serif;
    font-weight: 600;
    font-size: 19px;
    line-height: 33px;
    color: var(--ink);
  }
  .contact .sep { color: var(--brand-red); margin: 0 5px; }
</style>
</head>
<body>
  <section class="ad" aria-label="Anzeige Wachturm Technik">
    <svg class="ad__shapes" viewBox="0 0 1100 718" width="1100" height="718">
      <defs>
        <linearGradient id="photoTone" x1="0" y1="0" x2="0.4" y2="1">
          <stop offset="0" stop-color="#8cc3e8"/>
          <stop offset="0.45" stop-color="#d9b98a"/>
          <stop offset="0.8" stop-color="#8a9a5e"/>
          <stop offset="1" stop-color="#6f8a4a"/>
        </linearGradient>
      </defs>
      <polygon class="ad__photo" role="img"
        aria-label="Foto: Hand hält ein Smartphone mit Kamerabildern eines Home-Security-Systems vor einem Einfamilienhaus"
        points="0,0 423,0 559,282 379,718 0,718" fill="url(#photoTone)"/>
      <polyline points="423,0 559,282 379,718" fill="none" stroke="#d8412f" stroke-width="5"/>
    </svg>

    <div class="brand">
      <span class="brand__dot" aria-hidden="true"></span>
      <div>
        <div class="brand__name">Wachturm Technik</div>
        <div class="brand__claim">Schützen Sie sich und Ihr Eigentum</div>
      </div>
    </div>

    <h1 class="headline">MODERNE FUNKALARMANLAGEN</h1>

    <ul class="benefits">
      <li><svg viewBox="0 0 30 30"><rect x="2" y="6" width="22" height="22" fill="none" stroke="#d8412f" stroke-width="3"/><path d="M7 16 l6 6 L28 3" fill="none" stroke="#d8412f" stroke-width="4"/></svg>Individuelle Beratung</li>
      <li><svg viewBox="0 0 30 30"><rect x="2" y="6" width="22" height="22" fill="none" stroke="#d8412f" stroke-width="3"/><path d="M7 16 l6 6 L28 3" fill="none" stroke="#d8412f" stroke-width="4"/></svg>Onlineshop</li>
      <li><svg viewBox="0 0 30 30"><rect x="2" y="6" width="22" height="22" fill="none" stroke="#d8412f" stroke-width="3"/><path d="M7 16 l6 6 L28 3" fill="none" stroke="#d8412f" stroke-width="4"/></svg>Installation</li>
    </ul>

    <div class="funding">LBZ FÖRDERUNG MÖGLICH</div>

    <div class="services">
      <div class="service">
        <svg viewBox="0 0 56 38" width="56"><path d="M8 8 q-6 11 0 22 M13 12 q-3 7 0 14 M48 8 q6 11 0 22 M43 12 q3 7 0 14" fill="none" stroke="#222" stroke-width="2.5"/><rect x="18" y="5" width="20" height="28" rx="4" fill="#d8412f"/><g fill="#fff"><rect x="22" y="11" width="4" height="3"/><rect x="30" y="11" width="4" height="3"/><rect x="22" y="17" width="4" height="3"/><rect x="30" y="17" width="4" height="3"/><rect x="22" y="23" width="4" height="3"/><rect x="30" y="23" width="4" height="3"/></g></svg>
        Alarm
      </div>
      <div class="service">
        <svg viewBox="0 0 38 38" width="38"><path d="M3 12 V3 H12 M26 3 H35 V12 M35 26 V35 H26 M12 35 H3 V26" fill="none" stroke="#222" stroke-width="3"/><circle cx="19" cy="19" r="6" fill="#d8412f"/></svg>
        Video
      </div>
      <div class="service">
        <svg viewBox="0 0 46 38" width="46"><path d="M2 18 L16 6 L30 18" fill="none" stroke="#222" stroke-width="3"/><path d="M6 16 V34 H16" fill="none" stroke="#222" stroke-width="3"/><rect x="22" y="10" width="20" height="26" rx="3" fill="#222"/><path d="M32 14 L38 27 H26 Z" fill="#d8412f"/></svg>
        Hausautomation
      </div>
    </div>

    <address class="contact" style="font-style:normal">
      Lindenstraße 12<span class="sep">•</span>74999 Talhausen<span class="sep">•</span>07900-1234<br>
      www.wachturm-technik.de&nbsp; E-Mail: info@wachturm-technik.de
    </address>
  </section>
</body>
</html>
```